Redesign of business card for Cedar Ridge Mechanical

We are looking for a new design for our business cards for Cedar Ridge Mechanical. We are a plumbing & HVAC construction company, operating on the West Coast of Canada and USA. Logo attached.
Industry/Entity Type
Construction - Plumbing & HVAC
Contact Information for Business Card
Name, address, phone numbers, email, website address
Look and feel
Each slider illustrates characteristics of the customer's brand and the style your logo design should communicate.

```html
<!DOCTYPE html>
<html lang="en">
<head>
<meta charset="utf-8">
<title>Cedar Ridge Mechanical – Business Card</title>
<link rel="stylesheet" href="https://fonts.googleapis.com/css2?family=Oswald:wght@500;700&family=Lato:wght@400&display=swap">
<style>
  :root {
    --stage: #3a3a3a;
    --ink: #141414;
    --paper: #ffffff;
    --muted-on-dark: #9a9a9a;
    --rule: #1a1a1a;
  }
  * { margin: 0; padding: 0; box-sizing: border-box; }
  html, body { width: 1200px; height: 895px; overflow: hidden; }
  body { background: var(--stage); position: relative; font-family: "Lato", sans-serif; }

  .card {
    position: absolute;
    width: 630px;
    height: 360px;
    border-radius: 22px;
    box-shadow: 0 8px 24px rgba(0,0,0,0.35);
    overflow: hidden;
  }

  /* Back side */
  .card--back { left: 110px; top: 50px; background: var(--ink); }
  .card--back .brand {
    position: absolute; left: 0; right: 0; top: 150px;
    display: flex; align-items: center; justify-content: center; gap: 16px;
  }
  .brand-mark { width: 26px; height: 26px; border: 4px solid var(--paper); }
  .card--back .brand-name {
    font-family: "Oswald", sans-serif; font-weight: 700; font-size: 40px;
    letter-spacing: 2px; text-transform: uppercase; color: var(--paper);
  }

  /* Front side */
  .card--front { left: 460px; top: 485px; background: var(--paper); color: var(--ink); }
  .card--front .brand {
    position: absolute; right: 36px; top: 44px;
    display: flex; align-items: center; gap: 12px;
  }
  .card--front .brand-mark { width: 20px; height: 20px; border-width: 3px; border-color: var(--ink); }
  .card--front .brand-name {
    font-family: "Oswald", sans-serif; font-weight: 700; font-size: 28px;
    letter-spacing: 1.5px; text-transform: uppercase; color: var(--ink);
  }
  .rule { position: absolute; height: 2px; background: var(--rule); }
  .rule--brand { right: 36px; top: 108px; width: 320px; }
  .rule--person { left: 40px; top: 218px; width: 250px; }

  .address {
    position: absolute; right: 36px; top: 128px;
    text-align: right; font-size: 17px; line-height: 1.4;
  }

  .person { position: absolute; left: 40px; top: 146px; }
  .person-name {
    font-family: "Oswald", sans-serif; font-weight: 700; font-size: 28px;
    letter-spacing: 0.5px; text-transform: uppercase; line-height: 1.1;
  }
  .person-title { font-size: 18px; margin-top: 2px; }

  .contacts { position: absolute; left: 40px; top: 234px; list-style: none; }
  .contacts li { display: flex; align-items: center; gap: 12px; font-size: 17px; line-height: 30px; }
  .contacts svg { width: 16px; height: 16px; flex: none; }
</style>
</head>
<body>

<section class="card card--back" aria-label="Business card back">
  <div class="brand">
    <span class="brand-mark" aria-hidden="true"></span>
    <span class="brand-name">Cedar Ridge Mechanical</span>
  </div>
</section>

<section class="card card--front" aria-label="Business card front">
  <div class="brand">
    <span class="brand-mark" aria-hidden="true"></span>
    <span class="brand-name">Cedar Ridge Mechanical</span>
  </div>
  <div class="rule rule--brand"></div>

  <p class="address">2715 Alder Court<br>Suite 100, Fremont, CA 94538</p>

  <div class="person">
    <h1 class="person-name">Daniel Whitford</h1>
    <p class="person-title">Founder and CEO</p>
  </div>
  <div class="rule rule--person"></div>

  <ul class="contacts">
    <li>
      <svg viewBox="0 0 16 16" aria-hidden="true"><path fill="#141414" d="M2 5c0-2 2-3 6-3s6 1 6 3v1h-3V5H5v1H2zM4 7h8l2 7H2z"/><circle cx="8" cy="10.5" r="1.6" fill="#fff"/></svg>
      <span>604-555-0182</span>
    </li>
    <li>
      <svg viewBox="0 0 16 16" aria-hidden="true"><rect x="1" y="3" width="14" height="10" fill="#141414"/><path d="M1 3l7 6 7-6" fill="none" stroke="#fff" stroke-width="1.4"/></svg>
      <span>whitford@cedarridgemech.com</span>
    </li>
    <li>
      <svg viewBox="0 0 16 16" aria-hidden="true"><g fill="none" stroke="#141414" stroke-width="1.3"><circle cx="8" cy="8" r="6.5"/><ellipse cx="8" cy="8" rx="3" ry="6.5"/><path d="M1.5 8h13M2.5 4.8h11M2.5 11.2h11"/></g></svg>
      <span>www.cedarridgemech.com</span>
    </li>
  </ul>
</section>

</body>
</html>
```